Packaging design for a reclosable bag for our product

We have a logo, and we need to put it on packaging for our product and while we want the look to be simple, we want it to follow good design principles and also contain spaces for other product descriptions.

There will be 5 sizes at launch so I'd like 5 variations, one for each size.

I've included a few mockups of the type of bag that I made but they are all just rough ideas that I had.

I want the brand to look scientific and methodical and even a bit quirky, as in "wow this is a serious product but also a bit unusual."

```html
<!DOCTYPE html>
<html lang="en">
<head>
<meta charset="UTF-8">
<title>Bias Lighting Extra Large – Pouch Front</title>
<link href="https://fonts.googleapis.com/css2?family=Barlow:wght@500;600;700&display=swap" rel="stylesheet">
<style>
  :root {
    --backdrop: #2e2f33;
    --pouch: #111113;
    --ink: #f2f2f0;
    --seam: #232326;
  }
  html, body {
    margin: 0;
    padding: 0;
    width: 1200px;
    height: 833px;
    overflow: hidden;
    background: var(--backdrop);
  }
  .canvas {
    position: relative;
    width: 1200px;
    height: 833px;
    font-family: "Barlow", Arial, sans-serif;
  }
  .pouch {
    position: absolute;
    left: 353px;
    top: 110px;
    width: 493px;
    height: 668px;
    background: var(--pouch);
    color: var(--ink);
    overflow: hidden;
  }
  .pouch__zip {
    position: absolute;
    left: 0;
    right: 0;
    top: 72px;
    height: 4px;
    border-top: 1px solid var(--seam);
    border-bottom: 1px solid var(--seam);
  }
  .pouch__notch {
    position: absolute;
    top: 40px;
    width: 6px;
    height: 6px;
    background: var(--backdrop);
    border-radius: 50%;
  }
  .pouch__notch--left { left: -3px; }
  .pouch__notch--right { right: -3px; }
  .product-title {
    position: absolute;
    left: 24px;
    top: 178px;
    margin: 0;
    font-size: 29px;
    font-weight: 600;
    letter-spacing: 0.16em;
    line-height: 1;
  }
  .product-size {
    position: absolute;
    left: 65px;
    top: 216px;
    margin: 0;
    font-size: 11.5px;
    font-weight: 500;
    letter-spacing: 0.42em;
    line-height: 1;
  }
  .brand-name {
    position: absolute;
    left: 24px;
    top: 262px;
    margin: 0;
    font-size: 190px;
    font-weight: 700;
    line-height: 1;
    letter-spacing: 0.02em;
  }
  .spec {
    position: absolute;
    left: 225px;
    width: 210px;
    top: 526px;
    text-align: center;
  }
  .spec__length {
    margin: 0 0 8px;
    font-size: 16px;
    font-weight: 700;
    letter-spacing: 0.02em;
  }
  .spec__details {
    margin: 0;
    font-size: 10px;
    font-weight: 500;
    line-height: 1.3;
    letter-spacing: 0.02em;
  }
</style>
</head>
<body>
<main class="canvas">
  <section class="pouch" aria-label="Pouch front panel">
    <span class="pouch__notch pouch__notch--left"></span>
    <span class="pouch__notch pouch__notch--right"></span>
    <div class="pouch__zip"></div>

    <h1 class="product-title">BIAS LIGHTING</h1>
    <p class="product-size">EXTRA LARGUE</p>

    <p class="brand-name">KORA</p>

    <div class="spec">
      <p class="spec__length">5 METERS</p>
      <p class="spec__details">SIMULATED D65 CRI 90+<br>6500K WHITE BIAS LIGHTING</p>
    </div>
  </section>
</main>
</body>
</html>
```